Billboard design 8x3M RAVU (Spanish company)

We´re located in the south of Spain. We run a local telecom company.
We sell Fiber optic, and mobile phone lines mainly.
The billboard will have to be in Spanish, I would like the price to be something you spot on first sight when passing by in the car.
Our company color is blue, like in our logo which I will add. I will also add a example from what we currently have.
The new offer should be:
1000 megas + 100Gigas movil con llamadas ilimitadas. (meaning 1000Mb fiber optic speed and 100Gb data and unlimited calls for 1 mobile line)
Our details are: phone line 958 47 6620
Website: ra-vu.es

```html
<!DOCTYPE html>
<html lang="es">
<head>
<meta charset="utf-8">
<title>RAVU – Valla 8x3 m</title>
<link rel="stylesheet" href="https://fonts.googleapis.com/css2?family=Montserrat:wght@700;800;900&display=swap">
<style>
  :root {
    --page-bg: #1d2030;
    --board-deep: #0a3f66;
    --board-mid: #137ab8;
    --board-light: #2fb0ea;
    --band-light: #36b6ef;
    --band-dark: #143650;
    --yellow: #ffd500;
    --white: #ffffff;
    --flame-1: #ff8a1a;
    --flame-2: #ffb347;
    --flame-3: #e2560b;
  }
  * { margin: 0; padding: 0; box-sizing: border-box; }
  html, body {
    width: 1200px; height: 960px; overflow: hidden;
    background: var(--page-bg);
    font-family: "Montserrat", Arial, sans-serif;
  }
  .billboard {
    position: absolute; left: 40px; top: 270px;
    width: 1120px; height: 420px; overflow: hidden;
    background: linear-gradient(100deg, var(--board-deep) 0%, var(--board-mid) 45%, var(--board-light) 100%);
  }
  .headline { position: absolute; color: var(--yellow); font-weight: 900; line-height: .82; letter-spacing: -2px; }
  .headline .figure { display: block; font-size: 130px; }
  .headline .unit { display: block; font-size: 70px; letter-spacing: 0; }
  .speed { left: 28px; top: 20px; }
  .data { left: 430px; top: 50px; }
  .divider { position: absolute; left: 410px; top: 66px; width: 3px; height: 140px; background: var(--white); opacity: .85; }
  .mobile-line {
    position: absolute; left: 28px; top: 226px;
    color: var(--white); font-weight: 800; font-size: 44px; line-height: 1;
    text-transform: uppercase;
  }
  .bottom-band { position: absolute; left: 0; bottom: 0; width: 1120px; height: 76px; }
  .phone {
    position: absolute; left: 30px; bottom: 14px;
    display: flex; align-items: center; gap: 12px;
    color: var(--white); font-weight: 800; font-size: 44px; line-height: 1;
  }
  .site {
    position: absolute; left: 478px; bottom: 20px;
    display: flex; align-items: center; gap: 10px;
    color: var(--white); font-weight: 800; font-size: 34px; line-height: 1;
  }
  .launch-art {
    position: absolute; left: 760px; top: 178px; width: 330px; height: 222px;
    border-radius: 24px 24px 8px 8px;
    background: radial-gradient(ellipse at 50% 60%, var(--flame-2) 0%, var(--flame-1) 40%, var(--flame-3) 75%, rgba(226,86,11,0) 100%);
  }
  .brand { position: absolute; right: 36px; top: 104px; text-align: right; color: var(--white); }
  .brand .name { display: block; font-weight: 800; font-size: 44px; line-height: 1; letter-spacing: 2px; }
  .brand .services { display: block; font-weight: 700; font-size: 12px; margin-top: 4px; }
</style>
</head>
<body>
  <section class="billboard">
    <div class="headline speed"><span class="figure">1000</span><span class="unit">MEGAS+</span></div>
    <div class="divider"></div>
    <div class="headline data"><span class="figure">100</span><span class="unit">GIGAS</span></div>
    <p class="mobile-line">Movil con llamadas<br>ilimitadas.</p>

    <svg class="bottom-band" viewBox="0 0 1120 76" aria-hidden="true">
      <rect x="0" y="0" width="470" height="76" fill="var(--band-light)"/>
      <polygon points="430,0 700,0 740,76 470,76" fill="var(--band-dark)"/>
      <polygon points="430,0 470,76 430,76" fill="var(--band-light)"/>
    </svg>

    <div class="phone">
      <svg width="30" height="30" viewBox="0 0 24 24" aria-hidden="true"><path fill="var(--white)" d="M6.6 10.8a15.1 15.1 0 0 0 6.6 6.6l2.2-2.2a1 1 0 0 1 1-.25 11.4 11.4 0 0 0 3.6.57 1 1 0 0 1 1 1V20a1 1 0 0 1-1 1A17 17 0 0 1 3 4a1 1 0 0 1 1-1h3.5a1 1 0 0 1 1 1c0 1.25.2 2.45.57 3.57a1 1 0 0 1-.25 1z"/></svg>
      <span>958 47 6620</span>
    </div>
    <div class="site">
      <svg width="28" height="28" viewBox="0 0 24 24" aria-hidden="true"><g fill="none" stroke="var(--white)" stroke-width="2"><circle cx="12" cy="12" r="10"/><path d="M2 12h20M12 2c3 3 3 17 0 20M12 2c-3 3-3 17 0 20"/></g></svg>
      <span>ra-vu.es</span>
    </div>

    <div class="launch-art" role="img" aria-label="Cohete despegando desde la pantalla de un portátil entre una explosión de humo naranja"></div>

    <div class="brand">
      <span class="name">RAVU</span>
      <span class="services">Wifi | Fibra | Movil | Tv</span>
    </div>
  </section>
</body>
</html>
```